Lifestyle blog needs a website

I have a blog called Sunlit Ribbon Days. Logo has been done and I also have the wordpress site with a theme already added to it.

The basics are there but I need design expertise to put everything together, make it look great and ready for me to go and in and start using. Basically what is there at the moment needs to be deleted and start again (not a lot - just me playing around). I am not attached to the theme and am happy to go with whatever ideas you can come up with. At the moment I am looking at 3 lifestyle categories (Fashion, Fitness, Feelings) with a contact page so not an extensive build.

Audience will be women over 40 but please don't make this 'frumpy' - it is aimed at the women who act, look and feel younger than their age and so 'pink & fluffy' and 'old & solid' is not the look I am going for.

My deepest apologies for the delay in responding to designs. I had a family matter which took meant I was unable to spend the quality time required to review. I will therefore be reviewing and deciding over this weekend. Once again, my sincere apologies.

Women over 40

• Feeling of being targeted at old market

```html
<!DOCTYPE html>
<html lang="en">
<head>
<meta charset="utf-8">
<title>Sunlit Ribbon Days — Fashion &amp; Fitness</title>
<link href="https://fonts.googleapis.com/css2?family=Montserrat:wght@400;500;600;700&display=swap" rel="stylesheet">
<style>
:root{
  --red:#e8323c;
  --ink:#1d1d1d;
  --text:#555;
  --paper:#ffffff;
  --mist:#ececec;
  --card-line:#dcdcdc;
  --green:#5cb04a;
  --dark-btn:#333335;
  --footer:#0d0d0d;
}
*{box-sizing:border-box;margin:0;padding:0}
html,body{width:1200px;height:2821px;overflow:hidden}
body{position:relative;background:var(--paper);font-family:"Montserrat",Arial,sans-serif;color:var(--ink)}
.abs{position:absolute}

/* soft figure placeholders: faded pill shapes rather than hard blocks */
.figure{
  z-index:0;
  border-radius:48% 48% 38% 38% / 16% 16% 10% 10%;
  -webkit-mask-image:radial-gradient(ellipse 50% 50% at 50% 50%,#000 55%,transparent 100%);
  mask-image:radial-gradient(ellipse 50% 50% at 50% 50%,#000 55%,transparent 100%);
  opacity:.8;
}

/* header */
.brand{left:201px;top:26px;width:150px;font-weight:700;font-size:26px;line-height:1.05;color:var(--red);text-transform:uppercase;letter-spacing:.5px;z-index:3}
.main-nav{left:527px;top:36px;z-index:3}
.main-nav a{position:absolute;top:0;white-space:nowrap;font-size:12.5px;font-weight:500;color:var(--ink);text-decoration:none}
.main-nav a.active{color:var(--red)}

/* hero */
.hero-bg{left:0;top:0;width:1200px;height:781px}
.hero-title{left:330px;top:196px;width:540px;text-align:center;z-index:2}
.hero-title h1{font-size:27px;font-weight:600;color:var(--ink);letter-spacing:.3px;white-space:nowrap}
.hero-title h2{font-size:40px;font-weight:600;color:var(--red);margin-top:6px;letter-spacing:1px}
.hero-title p{font-size:12.5px;line-height:24px;color:var(--ink);width:420px;margin:10px auto 0}
.chev{width:28px;height:50px}
.round-down{width:40px;height:40px;border-radius:50%;border:2px solid var(--ink);background:var(--paper);display:flex;align-items:center;justify-content:center;z-index:2}

/* categories */
.section-title{width:1200px;left:0;text-align:center;font-weight:500;letter-spacing:.5px;z-index:2}
.cat-title{top:625px;font-size:24px;color:var(--red)}
.cat-btn{top:681px;width:252px;height:45px;display:flex;align-items:center;justify-content:center;gap:8px;color:#fff;font-size:17px;font-weight:500;text-transform:uppercase;z-index:2}
.cat-fashion{left:207px;background:var(--red)}
.cat-fitness{left:478px;background:var(--dark-btn)}
.cat-feelings{left:739px;background:var(--green)}

/* cards */
.latest-title{top:813px;font-size:26px;color:var(--ink)}
.card{background:var(--paper);border:1px solid var(--card-line);overflow:hidden;z-index:1}
.card .media{width:100%}
.card .body{padding:14px 14px 0}
.card h3{font-size:13px;font-weight:600;color:var(--red);margin-bottom:8px}
.card p{font-size:9px;line-height:14px;color:var(--text)}
.card .more{display:block;margin-top:8px;font-size:8.5px;font-weight:700;color:var(--ink);text-transform:uppercase}
.wide-card{background:#f1f1f1;border:none}
.wide-card .body{padding:10px 22px 0 22px;position:relative}
.wide-card h3{font-size:12.5px;font-weight:500;color:var(--ink);margin-bottom:2px}
.wide-card p{font-size:10px;line-height:14px;color:var(--text)}
.mini-arrow{position:absolute;right:14px;top:16px;width:24px;height:24px;border-radius:50%;border:1.5px solid #777;display:flex;align-items:center;justify-content:center}

/* top blogs */
.top-band{left:0;top:1492px;width:1200px;height:440px}
.top-title{top:1528px;font-size:26px;color:#fff}
.slider-arrow{width:42px;height:42px;border-radius:50%;border:2px solid #fff;background:rgba(0,0,0,.45);display:flex;align-items:center;justify-content:center;z-index:2}

/* feature */
.feature h3{font-size:13px;line-height:19px;font-weight:600;color:var(--red);margin-bottom:10px}
.feature p{font-size:9.5px;line-height:15px;color:var(--text);margin-bottom:7px}

/* footer */
.social{top:2689px;width:29px;height:29px;border-radius:50%;border:1.5px solid #fff}
.foot-nav{top:2738px;left:0;width:1200px;display:flex;justify-content:center;gap:34px}
.foot-nav a{font-size:12.5px;font-weight:500;color:#fff;text-decoration:none}
.copyright{top:2766px;left:0;width:1200px;text-align:center;font-size:10px;color:#bbb}
</style>
</head>
<body>

<svg class="abs hero-bg" viewBox="0 0 1200 781" aria-hidden="true">
  <defs>
    <linearGradient id="heroGrad" x1="0" y1="0" x2="0" y2="1">
      <stop offset="0" stop-color="#ffffff"/>
      <stop offset="1" stop-color="#e9e9e9"/>
    </linearGradient>
  </defs>
  <rect width="1200" height="781" fill="url(#heroGrad)"/>
  <polygon points="0,455 600,566 1200,455 1200,781 0,781" fill="#ececec"/>
  <polygon points="0,451 600,562 1200,451 1200,465 600,576 0,465" fill="#e8323c"/>
</svg>

<header>
  <div class="abs brand">Sunlit Ribbon Days</div>
  <nav class="abs main-nav">
    <a class="active" href="#" style="left:0">HOME</a>
    <a href="#" style="left:67px">ABOUT US</a>
    <a href="#" style="left:161px">BLOGS</a>
    <a href="#" style="left:231px">CATEGORY</a>
    <a href="#" style="left:327px">PHOTOS</a>
    <a href="#" style="left:408px">CONTACT</a>
  </nav>
</header>

<div class="abs figure" role="img" aria-label="Cut-out photo of a smiling blonde woman in a red jacket" style="left:180px;top:132px;width:200px;height:404px;background:linear-gradient(180deg,#f1d9b8 0%,#e6bfa0 25%,#d8333c 50%,#c22a33 100%)"></div>
<div class="abs figure" role="img" aria-label="Cut-out photo of a dark-haired woman in a red dress" style="left:848px;top:117px;width:200px;height:419px;background:linear-gradient(180deg,#5a3a2c 0%,#e0b9a0 28%,#d4303a 55%,#b8252e 100%)"></div>

<div class="abs hero-title">
  <h1>WELCOME TO SUNLIT RIBBON DAYS</h1>
  <h2>FASHION &amp; FITNESS</h2>
  <p>Morbi diam mauris viverra in gravida eu mattis in ante Morbi eget arcu Morbi porta libero id ullamcorper nonummy</p>
</div>

<svg class="abs chev" style="left:110px;top:218px" viewBox="0 0 28 50" aria-hidden="true"><polyline points="24,2 4,25 24,48" fill="none" stroke="#666" stroke-width="2.5"/></svg>
<svg class="abs chev" style="left:1096px;top:218px" viewBox="0 0 28 50" aria-hidden="true"><polyline points="4,2 24,25 4,48" fill="none" stroke="#666" stroke-width="2.5"/></svg>

<div class="abs round-down" style="left:580px;top:512px"><svg width="16" height="10" viewBox="0 0 16 10" aria-hidden="true"><polyline points="2,2 8,8 14,2" fill="none" stroke="#1d1d1d" stroke-width="2.2"/></svg></div>

<h2 class="abs section-title cat-title">OUR CATEGORY</h2>
<div class="abs cat-btn cat-fashion">
  <svg width="30" height="24" viewBox="0 0 30 24" aria-hidden="true"><path d="M3 6 L3 20 L6 20 L6 13 C10 14 14 20 20 21 L28 21 C28 18 25 17 21 16 C15 14 10 6 3 6 Z" fill="none" stroke="#fff" stroke-width="1.6"/></svg>
  Fashion
</div>
<div class="abs cat-btn cat-fitness">
  <svg width="34" height="20" viewBox="0 0 34 20" aria-hidden="true"><g fill="none" stroke="#fff" stroke-width="1.8"><rect x="4" y="3" width="5" height="14"/><rect x="25" y="3" width="5" height="14"/><line x1="9" y1="10" x2="25" y2="10"/><line x1="1" y1="10" x2="4" y2="10"/><line x1="30" y1="10" x2="33" y2="10"/></g></svg>
  Fitness
</div>
<div class="abs cat-btn cat-feelings">
  <svg width="22" height="28" viewBox="0 0 22 28" aria-hidden="true"><g fill="none" stroke="#fff" stroke-width="1.6"><path d="M11 2 C5 2 2 6 2 10 C2 14 6 16 7 20 L15 20 C16 16 20 14 20 10 C20 6 17 2 11 2 Z"/><line x1="7" y1="23" x2="15" y2="23"/><line x1="8" y1="26" x2="14" y2="26"/></g></svg>
  Feelings
</div>

<div class="abs figure" role="img" aria-label="Cut-out photo of a woman in a short black dress" style="left:0;top:734px;width:200px;height:761px;background:linear-gradient(180deg,#6b4a36 0%,#e2c0a4 16%,#1c1c1c 30%,#222 58%,#d7b497 72%,#d7b497 92%,#222 100%)"></div>
<div class="abs figure" role="img" aria-label="Cut-out photo of a fit woman in black sportswear holding a dumbbell" style="left:1000px;top:818px;width:200px;height:677px;background:linear-gradient(180deg,#3a2a22 0%,#c79a7e 20%,#1b1b1b 40%,#262626 100%)"></div>

<h2 class="abs section-title latest-title">LATEST BLOGS</h2>

<article class="abs card wide-card" style="left:207px;top:869px;width:271px;height:260px">
  <div class="media" role="img" aria-label="Photo of a person in a meadow at sunset" style="height:203px;background:linear-gradient(180deg,#f3e1b8 0%,#d7b071 45%,#7c6a33 75%,#4f4526 100%)"></div>
  <div class="body"><h3>Blogs Title here</h3><p>Morbi diam mauris viverra in gravida</p>
    <span class="mini-arrow"><svg width="8" height="10" viewBox="0 0 8 10" aria-hidden="true"><polyline points="2,1 6,5 2,9" fill="none" stroke="#777" stroke-width="1.6"/></svg></span></div>
</article>
<article class="abs card wide-card" style="left:487px;top:869px;width:506px;height:260px">
  <div class="media" role="img" aria-label="Photo of a woman in a white skirt above a city tower" style="height:203px;background:linear-gradient(135deg,#37b6c8 0%,#59c6d4 45%,#e8e1cf 70%,#3fb1c4 100%)"></div>
  <div class="body"><h3>Duis quam Nam eget lacus</h3><p>Morbi diam mauris viverra in gravida eu mattis in ante Morbi eget</p>
    <span class="mini-arrow"><svg width="8" height="10" viewBox="0 0 8 10" aria-hidden="true"><polyline points="2,1 6,5 2,9" fill="none" stroke="#777" stroke-width="1.6"/></svg></span></div>
</article>

<article class="abs card" style="left:207px;top:1170px;width:254px;height:277px">
  <div class="media" role="img" aria-label="Photo of a woman in a wide hat and sunglasses" style="height:162px;background:linear-gradient(180deg,#d9d9d9 0%,#3a3a3a 50%,#8d8d8d 100%)"></div>
  <div class="body"><h3>Blogs Title here</h3><p>Morbi diam mauris viverra in gravida eu mattis in ante Morbi eget arcu Morbi porta libero id ullamcorper nonummy nibh ligula pulvinar metus eget</p><span class="more">Read more</span></div>
</article>
<article class="abs card" style="left:478px;top:1170px;width:252px;height:277px">
  <div class="media" role="img" aria-label="Photo of a woman in a pink dress and sun hat" style="height:162px;background:linear-gradient(90deg,#1f6f78 0%,#2c8b93 40%,#e25a8f 55%,#2a8890 70%,#1e6a72 100%)"></div>
  <div class="body"><h3>Blogs Title here</h3><p>Morbi diam mauris viverra in gravida eu mattis in ante Morbi eget arcu Morbi porta libero id ullamcorper nonummy nibh ligula pulvinar metus eget</p><span class="more">Read more</span></div>
</article>
<article class="abs card" style="left:747px;top:1170px;width:250px;height:277px">
  <div class="media" role="img" aria-label="Photo of a woman in a summer dress under a tree" style="height:162px;background:linear-gradient(180deg,#e9dca0 0%,#8ea246 40%,#c6874f 70%,#5e6b2c 100%)"></div>
  <div class="body"><h3>Blogs Title here</h3><p>Morbi diam mauris viverra in gravida eu mattis in ante Morbi eget arcu Morbi porta libero id ullamcorper nonummy nibh ligula pulvinar metus eget</p><span class="more">Read more</span></div>
</article>

<div class="abs top-band" role="img" aria-label="Dark toned background photo of fashionable women" style="background:linear-gradient(90deg,#3c3c3e 0%,#545456 35%,#4a4a4c 65%,#353537 100%);z-index:1"></div>
<svg class="abs" style="left:588px;top:1488px;z-index:2" width="24" height="12" viewBox="0 0 24 12" aria-hidden="true"><polygon points="0,0 24,0 12,10" fill="#fff"/></svg>
<h2 class="abs section-title top-title">TOP BLOGS</h2>

<div class="abs slider-arrow" style="left:148px;top:1689px"><svg width="10" height="14" viewBox="0 0 10 14" aria-hidden="true"><polyline points="8,1 2,7 8,13" fill="none" stroke="#fff" stroke-width="2"/></svg></div>
<div class="abs slider-arrow" style="left:1002px;top:1689px"><svg width="10" height="14" viewBox="0 0 10 14" aria-hidden="true"><polyline points="2,1 8,7 2,13" fill="none" stroke="#fff" stroke-width="2"/></svg></div>

<article class="abs card" style="left:201px;top:1580px;width:252px;height:275px;border:none;z-index:2">
  <div class="media" role="img" aria-label="Photo of a woman stretching on a yoga mat" style="height:160px;background:linear-gradient(180deg,#e8d3b4 0%,#b86aa8 45%,#6c3f7e 75%,#d9c1a2 100%)"></div>
  <div class="body"><h3>Blogs Title here</h3><p>Morbi diam mauris viverra in gravida eu mattis in ante Morbi eget arcu Morbi porta libero id ullamcorper nonummy nibh ligula pulvinar metus eget</p><span class="more">Read more</span></div>
</article>
<article class="abs card" style="left:472px;top:1580px;width:252px;height:275px;border:none;z-index:2">
  <div class="media" role="img" aria-label="Photo of a woman sitting on a boat facing a tropical sea" style="height:160px;background:linear-gradient(180deg,#2e86d6 0%,#7ec4ec 40%,#22b3c2 70%,#d9b98a 100%)"></div>
  <div class="body"><h3>Blogs Title here</h3><p>Morbi diam mauris viverra in gravida eu mattis in ante Morbi eget arcu Morbi porta libero id ullamcorper nonummy nibh ligula pulvinar metus eget</p><span class="more">Read more</span></div>
</article>
<article class="abs card" style="left:743px;top:1580px;width:252px;height:275px;border:none;z-index:2">
  <div class="media" role="img" aria-label="Photo of women doing a workout in a gym" style="height:160px;background:linear-gradient(180deg,#9c7b61 0%,#d8c6b2 40%,#7a6a5d 75%,#4e4741 100%)"></div>
  <div class="body"><h3>Blogs Title here</h3><p>Morbi diam mauris viverra in gravida eu mattis in ante Morbi eget arcu Morbi porta libero id ullamcorper nonummy nibh ligula pulvinar metus eget</p><span class="more">Read more</span></div>
</article>

<div class="abs figure" role="img" aria-label="Cut-out photo of a laughing red-haired woman in a checked shirt" style="left:0;top:2182px;width:190px;height:451px;background:linear-gradient(180deg,#b5532c 0%,#e2b495 26%,#d7d7d9 46%,#9a9aa2 70%,#f1f1f1 100%)"></div>
<div class="abs figure" role="img" aria-label="Cut-out photo of a woman in sportswear stretching her arms" style="left:1000px;top:2248px;width:200px;height:423px;background:linear-gradient(180deg,#e7c7ad 0%,#d9b49a 30%,#2a2a2a 58%,#3a3a3a 100%)"></div>

<article class="abs card feature" style="left:199px;top:1971px;width:518px;height:277px;display:flex">
  <div role="img" aria-label="Photo of a smiling woman in a coral dress" style="width:254px;height:100%;flex:none;background:linear-gradient(180deg,#46c0c0 0%,#63cbc8 35%,#f05b5b 60%,#e34a52 80%,#47bfbf 100%)"></div>
  <div class="body" style="width:264px;padding:28px 20px 0 22px">
    <h3>Pellentesque faucibus Ut accumsan ultricies elit Maecenas at justo id velit placer</h3>
    <p>Vivamus porttitor purus nisi eleifend libero a tempus libero lectus feugiat etuer augue nisi quis lacus Ut ac mi quis lacus mollis</p>
    <p>tempus eros Curabitur vel mi sit amet magna malesuada ultrices Ut nisi erat fermentum vel congue id euismod in elit Fusce ultricies orci ac feugiat suscipit leo massa sodales velit et lee</p>
    <span class="more">Read more</span>
  </div>
</article>
<article class="abs card" style="left:739px;top:1971px;width:254px;height:277px">
  <div class="media" role="img" aria-label="Photo of a woman raising her arms at sunset" style="height:160px;background:linear-gradient(180deg,#f6ead8 0%,#f0c39a 45%,#e07d4f 75%,#c9663f 100%)"></div>
  <div class="body"><h3>Blogs Title here</h3><p>Morbi diam mauris viverra in gravida eu mattis in ante Morbi eget arcu Morbi porta libero id ullamcorper nonummy nibh ligula pulvinar metus eget</p><span class="more">Read more</span></div>
</article>

<article class="abs card" style="left:199px;top:2265px;width:252px;height:274px">
  <div class="media" role="img" aria-label="Photo of a woman with a flowing white scarf on a beach" style="height:162px;background:linear-gradient(180deg,#bcd7ec 0%,#e9f1f7 45%,#6fa3c4 75%,#cfc3ac 100%)"></div>
  <div class="body"><h3>Blogs Title here</h3><p>Morbi diam mauris viverra in gravida eu mattis in ante Morbi eget arcu Morbi porta libero id ullamcorper nonummy nibh ligula pulvinar metus eget</p><span class="more">Read more</span></div>
</article>
<article class="abs card" style="left:468px;top:2265px;width:252px;height:274px">
  <div class="media" role="img" aria-label="Photo of a woman in a long patterned gown by a building" style="height:162px;background:linear-gradient(90deg,#cfc8b8 0%,#4e9aa4 40%,#2f7f8f 60%,#a7b3b8 100%)"></div>
  <div class="body"><h3>Blogs Title here</h3><p>Morbi diam mauris viverra in gravida eu mattis in ante Morbi eget arcu Morbi porta libero id ullamcorper nonummy nibh ligula pulvinar metus eget</p><span class="more">Read more</span></div>
</article>
<article class="abs card" style="left:739px;top:2265px;width:254px;height:274px">
  <div class="media" role="img" aria-label="Photo of a woman doing push-ups in a gym" style="height:162px;background:linear-gradient(180deg,#e2e2e2 0%,#b9b9b9 40%,#5d5d5d 70%,#9d9d9d 100%)"></div>
  <div class="body"><h3>Blogs Title here</h3><p>Morbi diam mauris viverra in gravida eu mattis in ante Morbi eget arcu Morbi porta libero id ullamcorper nonummy nibh ligula pulvinar metus eget</p><span class="more">Read more</span></div>
</article>

<div class="abs round-down" style="left:573px;top:2559px;border-color:#777"><svg width="16" height="10" viewBox="0 0 16 10" aria-hidden="true"><polyline points="2,2 8,8 14,2" fill="none" stroke="#555" stroke-width="2"/></svg></div>

<svg class="abs" style="left:0;top:2630px;z-index:2" width="1200" height="191" viewBox="0 0 1200 191" aria-hidden="true">
  <polygon points="0,50 600,0 1200,50 1200,191 0,191" fill="#e8323c"/>
  <polygon points="0,64 600,14 1200,64 1200,191 0,191" fill="#0d0d0d"/>
</svg>
<footer style="position:relative;z-index:3">
  <span class="abs social" style="left:524px" aria-label="Social link"></span>
  <span class="abs social" style="left:560px" aria-label="Social link"></span>
  <span class="abs social" style="left:597px" aria-label="Social link"></span>
  <span class="abs social" style="left:634px" aria-label="Social link"></span>
  <nav class="abs foot-nav">
    <a href="#">HOME</a><a href="#">ABOUT US</a><a href="#">BLOGS</a><a href="#">CATEGORY</a><a href="#">PHOTOS</a><a href="#">CONTACT</a>
  </nav>
  <p class="abs copyright">© 2018 Sunlit Ribbon Days. All right reserved. Terms of Use</p>
</footer>

</body>
</html>
```